Business Cards for IT Consulting Company (Managed Service Provider)

I am looking to have some business cards printed and would like some designs. We are an IT Consulting company based in Vancouver BC. I would like a nice clean and modern look to the cards. I have uploaded all the versions of my logo so parts can be used as needed. Here is a snippit from our website homepage:

Quillbrook Networks Ltd. is an IT Solutions Partner located in Vancouver BC, Canada. We offer IT solutions and support to customers in the greater Vancouver Area. With expertise in Microsoft platforms, as well as Linux and Mac OSX and over 12 years experience in the IT industry, Quillbrook Networks is dedicated to offering our clients top quality service and products. We take pride in the solutions we offer our customers. The greatest compliment a client can give us is to recommend our services.

Quillbrook Networks Ltd. offers a wide range of IT services from onsite service to remote support and managed service solutions. This allows clients to choose the support path that best suits their company’s needs. Supporting many different sized companies from small to enterprise level over the past 12 years Quillbrook Networks has the experience and expertise needed to ensure things run smoothly. Allowing our clients to focus on doing business.

Revolutionizing the way IT services are delivered.

Quillbrook Networks is dedicated to providing our clients with IT solutions that work and grow with them for years to come. This philosophy helps save money in the long run instead of replacing equipment constantly. Far too often IT solutions are not well thought out and while possibly solving the problem at hand, require replacement due to growth or quality within a very short time frame. Quillbrook Networks takes pride in providing solutions that will last and be able to accommodate growth without the need for replacement.

Industry/Entity Type

Information Technology

Contact Information for Business Card

Quillbrook Networks Ltd.
(Employee Name)
Eml: (Employees Email Address)
Web: quillbrook.me
Ph: 604-555-0148

Font styles to use
Serif
Sans Serif

Requirements
Must have
• The Company logo and company colors.
Nice to have
• - Our tag line: "Revolutionizing IT Services" or "Revolutionizing the way IT services are delivered."
• - Also I really like the idea of nature and technology together blending which is sort of where my logo came from so integrating that somehow onto the business cards would be great.

```html
<!DOCTYPE html>
<html lang="en">
<head>
<meta charset="utf-8">
<title>Quillbrook Networks Ltd. – Business Cards</title>
<link rel="stylesheet" href="https://fonts.googleapis.com/css2?family=Montserrat:wght@400;500;600;700&display=swap">
<style>
  :root {
    --brand-blue: #1aa3e8;
    --card-grey: #5f6062;
    --paper: #ffffff;
    --backdrop: #e6e7e9;
    --text-light: #ffffff;
  }
  * { box-sizing: border-box; margin: 0; padding: 0; }
  html, body { width: 1200px; height: 900px; overflow: hidden; }
  body {
    background: var(--backdrop);
    font-family: "Montserrat", sans-serif;
    position: relative;
  }
  .card {
    position: absolute;
    left: 300px;
    width: 600px;
    height: 343px;
    border-radius: 18px;
    background: var(--paper);
    overflow: hidden;
    box-shadow: 0 10px 28px rgba(0, 0, 0, 0.18);
  }
  .card--front { top: 70px; }
  .card--back { top: 487px; }

  /* Front card */
  .front-wordmark {
    position: absolute;
    top: 105px;
    left: 0;
    right: 0;
    display: flex;
    justify-content: center;
    align-items: center;
    gap: 14px;
    color: var(--brand-blue);
    font-weight: 600;
    font-size: 34px;
  }
  .brand-square {
    width: 30px;
    height: 30px;
    background: var(--brand-blue);
    flex: none;
  }
  .tagline-band {
    position: absolute;
    left: 0;
    right: 0;
    top: 270px;
    height: 30px;
    background: var(--brand-blue);
    color: var(--text-light);
    font-size: 15px;
    font-weight: 500;
    letter-spacing: 0.5px;
    display: flex;
    align-items: center;
    justify-content: center;
  }
  .edge-stripe {
    position: absolute;
    left: 0;
    right: 0;
    bottom: 0;
    height: 14px;
    background: var(--brand-blue);
  }

  /* Back card */
  .back-shape { position: absolute; inset: 0; }
  .back-wordmark {
    position: absolute;
    top: 98px;
    left: 70px;
    display: flex;
    align-items: center;
    gap: 12px;
    color: var(--brand-blue);
    font-weight: 600;
    font-size: 26px;
  }
  .back-wordmark .brand-square { width: 24px; height: 24px; }
  .holder {
    position: absolute;
    right: 250px;
    top: 248px;
    text-align: right;
  }
  .holder-name {
    color: var(--brand-blue);
    font-weight: 700;
    font-size: 21px;
    letter-spacing: 1px;
  }
  .holder-role {
    color: var(--text-light);
    font-weight: 500;
    font-size: 12px;
    letter-spacing: 1px;
    margin-top: 2px;
  }
  .divider {
    position: absolute;
    left: 366px;
    top: 228px;
    width: 1px;
    height: 78px;
    background: rgba(255, 255, 255, 0.55);
  }
  .contact-list {
    position: absolute;
    left: 384px;
    top: 228px;
    list-style: none;
    color: var(--text-light);
    font-size: 13px;
    font-weight: 500;
  }
  .contact-list li {
    display: flex;
    align-items: center;
    gap: 8px;
    height: 26px;
  }
  .contact-icon { width: 11px; height: 11px; flex: none; }
</style>
</head>
<body>

  <section class="card card--front" aria-label="Card front">
    <div class="front-wordmark"><span class="brand-square"></span>Quillbrook</div>
    <div class="tagline-band">Revolutionizing IT Services</div>
    <div class="edge-stripe"></div>
  </section>

  <section class="card card--back" aria-label="Card back">
    <svg class="back-shape" viewBox="0 0 600 343" width="600" height="343" aria-hidden="true">
      <path d="M0 246 Q330 256 600 46 L600 343 L0 343 Z" fill="var(--card-grey)"/>
      <path d="M0 240 Q330 250 600 40" fill="none" stroke="var(--brand-blue)" stroke-width="5"/>
    </svg>

    <div class="back-wordmark"><span class="brand-square"></span>Quillbrook Networks Ltd.</div>

    <div class="holder">
      <div class="holder-name">MARIN OKAFOR</div>
      <div class="holder-role">DIRECTOR</div>
    </div>

    <div class="divider"></div>

    <ul class="contact-list">
      <li>
        <svg class="contact-icon" viewBox="0 0 24 24" aria-hidden="true"><path fill="var(--brand-blue)" d="M6.6 10.8a15.1 15.1 0 0 0 6.6 6.6l2.2-2.2a1 1 0 0 1 1-.25 11.4 11.4 0 0 0 3.6.57 1 1 0 0 1 1 1V20a1 1 0 0 1-1 1A17 17 0 0 1 3 4a1 1 0 0 1 1-1h3.5a1 1 0 0 1 1 1c0 1.25.2 2.45.57 3.57a1 1 0 0 1-.25 1z"/></svg>
        604-555-0148
      </li>
      <li>
        <svg class="contact-icon" viewBox="0 0 24 24" aria-hidden="true"><rect x="2" y="5" width="20" height="14" rx="2" fill="none" stroke="var(--brand-blue)" stroke-width="2.5"/><path d="M3 6l9 7 9-7" fill="none" stroke="var(--brand-blue)" stroke-width="2.5"/></svg>
        info@marinokafor.com
      </li>
      <li>
        <svg class="contact-icon" viewBox="0 0 24 24" aria-hidden="true"><circle cx="12" cy="12" r="9.5" fill="none" stroke="var(--brand-blue)" stroke-width="2.5"/><path d="M2.5 12h19M12 2.5c3 3 3 16 0 19M12 2.5c-3 3-3 16 0 19" fill="none" stroke="var(--brand-blue)" stroke-width="2"/></svg>
        www.quillbrook.me
      </li>
    </ul>
  </section>

</body>
</html>
```